Maple Beacon Website

We are starting a marketing company and to do that we need a website! We want a website that will inspire and persuade to bring out the awesomeness in our clients.
What we want to see:
- Inspirational and persuasive imagery that relate to Branding.
- No cliche images eg. business man, suits and hand shakes
- We want to transform and educate our clients.
- We want to show them the path and would like our website to really act as a guide that guides them step by step through our process.
- We want the portray that we are an investment but not have a pretentious way to it. We put our heart into every project and that is how we treat our clients.
-When you submit your design please include what platform you have created for. Preference would be Wordpress or Joobla.

We have included the psd file for the wire frame, logo files, font files, site map and a link to a video we create to give you more information on what we would like to see. http://clipvault.example/t/qk82LmZpr

Feel free to make small modification to the logos if you think it will improve it. Your creativity and advice is most welcome.
Updates

One thing we forgot. We would like to have our contact information near the top of the website as well as at the bottom.  Here is out contact info:

Email: info@maplebeacon.example
Phone: 587-555-0142

Project Deadline Extended
Reason: As we are new with the platform and that we want to optimize our results, we decided to extend the deadline by 15 days. Thanks!

Target Market(s)

28-60, Male and Female, Oil field, Local Businesses, Dentists, Chiropractors, Hair salon, Construction/Renovation, Events etc

Industry/Entity Type

Investment

Requirements
Must have
• - 4 Inspirational and persuasive Imagery for the top portion of the website
- Must have a feel as if your not on a website an example of this is linked below.
http://www.artbidhub.example/design/402957/web-design-by-lena-torvik
Nice to have
• - Creative advice from you.
- Creative buttons for Get Free Quote and Subscribe buttons. Something out of the box that draws peoples attention. eg. a 'B' button. Just and example but still something related to branding.
Should not have
• No Cliches

```html
<!DOCTYPE html>
<html lang="en">
<head>
<meta charset="utf-8">
<title>Maple Beacon</title>
<link rel="stylesheet" href="https://fonts.googleapis.com/css2?family=Open+Sans:wght@400;600;700&family=Fredoka:wght@600&display=swap">
<style>
:root{
  --bar-dark:#3e3f37;
  --bar-light:#8a8b80;
  --page:#f7f7f7;
  --ink:#2e2e2e;
  --body:#555;
  --green:#5c9a1b;
  --green-light:#8dc63f;
  --green-dark:#3e7a12;
  --panel:#e4e4e4;
  --grey-btn:#9a9a9a;
  --footer-top:#9a9a9a;
  --footer-bottom:#3a3a3a;
}
*{box-sizing:border-box;margin:0;padding:0}
html,body{width:1200px;height:1113px;overflow:hidden}
body{background:var(--page);font-family:"Open Sans",sans-serif;color:var(--body);position:relative}
.topbar{position:absolute;left:0;top:0;width:1200px;height:42px;background:linear-gradient(#8e8f84,#4a4b42);color:#fff;font-size:18px;display:flex;justify-content:flex-end;align-items:center;padding-right:18px;gap:6px}
.topbar svg,.footer-contact svg{width:16px;height:14px;fill:#111;vertical-align:-2px;margin-right:4px}
.phone{font-weight:700}
.hero{position:absolute;left:0;top:42px;width:1200px;height:381px;background:radial-gradient(ellipse at 62% 40%,#fafafa 0%,#ececec 55%,#dcdcdc 100%);border-bottom:1px solid #d0d0d0}
.side{position:absolute;left:118px;top:42px;width:230px;height:324px;background:linear-gradient(#fbfbfb,#e6e6e6 70%,rgba(230,230,230,0))}
.brand{display:flex;align-items:center;gap:8px;padding:22px 0 0 16px;font-family:"Fredoka",sans-serif;font-size:26px;color:#5a5a5a}
.brand i{width:16px;height:16px;border-radius:50%;background:var(--green-light)}
.tagline{font-style:italic;font-size:13px;color:#333;padding:10px 0 0 44px;font-weight:600}
.mainnav{list-style:none;padding:22px 0 0 17px}
.mainnav li{font-weight:700;font-size:16px;color:var(--ink);height:37.5px}
.steps{position:absolute;right:18px;top:112px;list-style:none;text-align:right}
.steps li{font-family:"Fredoka",sans-serif;font-size:18px;color:var(--ink);height:69px;display:flex;align-items:center;justify-content:flex-end;gap:8px;line-height:1}
.steps li::after{content:"";width:17px;height:17px;border-radius:50%;background:radial-gradient(circle at 35% 35%,#bbb,#555)}
.steps li.active{color:var(--green)}
.steps li.active::after{background:radial-gradient(circle at 35% 35%,#c6f07a,#4f8a12)}
.box{position:absolute;top:447px;height:93px;background:var(--panel);box-shadow:0 12px 10px -8px rgba(0,0,0,.25)}
.connect{left:120px;width:228px;text-align:center}
.box h2{font-size:21px;font-weight:700;color:#555;padding-top:16px}
.socials{display:flex;justify-content:center;gap:7px;margin-top:4px}
.socials span{width:32px;height:32px;border-radius:3px}
.newsletter{left:361px;width:711px;text-align:center}
.newsletter h2 em{font-style:normal;color:var(--green)}
.signup{display:flex;justify-content:center;gap:4px;margin-top:6px}
.signup .field{width:500px;height:38px;background:#fff;border:1px solid #c8c8c8;border-radius:3px;text-align:left;font-size:14px;color:#666;padding:6px 9px}
.signup .btn{width:98px;height:38px;background:linear-gradient(#b8b8b8,#8c8c8c);color:#fff;font-weight:700;font-size:16px;border-radius:3px;display:flex;align-items:center;justify-content:center}
.welcome{position:absolute;left:123px;top:580px;width:960px}
.welcome h1{font-family:"Fredoka",sans-serif;font-size:25px;color:var(--ink);letter-spacing:.3px}
.welcome h3{color:var(--green);font-size:16px;font-weight:700;margin:15px 0 0 2px}
.welcome p{font-size:15.5px;line-height:21px;margin-left:2px}
.ticks{list-style:none;margin:9px 0 0 4px}
.ticks li{font-size:16px;color:#333;height:34.5px;display:flex;align-items:center;gap:11px}
.ticks svg{width:19px;height:19px}
.closing{margin-top:18px}
.quote{position:absolute;left:919px;top:832px;width:157px;height:39px;background:linear-gradient(var(--green-light),var(--green-dark));color:#fff;font-weight:700;font-size:15.5px;border-radius:3px;display:flex;align-items:center;justify-content:center}
.footer{position:absolute;left:0;top:994px;width:1200px;height:119px;background:linear-gradient(var(--footer-top),var(--footer-bottom));color:#fff}
.footnav{position:absolute;left:123px;top:30px;display:flex;gap:14px;font-size:17px;font-weight:600}
.copy{position:absolute;left:123px;top:57px;color:var(--green-light);font-size:17px}
.footer-contact{position:absolute;right:124px;top:30px;font-size:18px}
</style>
</head>
<body>
<header class="topbar">
  <svg viewBox="0 0 16 12"><path d="M0 0h16v12H0z M0 0l8 6 8-6" stroke="#8e8f84" stroke-width="1"/></svg>
  <span>info@maplebeacon.example</span><span>|</span>
  <svg viewBox="0 0 16 16"><path d="M3 1l3 3-2 2c1 2 3 4 5 5l2-2 3 3-2 3C7 14 2 9 0 3z"/></svg>
  <span class="phone">587-555-0142</span>
</header>

<div class="hero" role="img" aria-label="Photo of three glass fishbowls with a goldfish leaping from one bowl toward the next"></div>

<aside class="side">
  <div class="brand"><i></i>Maple Beacon</div>
  <div class="tagline">Because You're Awesome!</div>
  <ul class="mainnav">
    <li>STRATEGY</li><li>PORTFOLIO</li><li>ABOUT US</li><li>CONTACT US</li><li>BLOG</li>
  </ul>
</aside>

<ul class="steps">
  <li>MAPLE BEACON</li><li>BE FOUND</li><li>CONNECT</li><li class="active">GET GROWING</li>
</ul>

<section class="box connect">
  <h2>CONNECT WITH US</h2>
  <div class="socials">
    <span style="background:#3b5998"></span><span style="background:#4fc1e9"></span><span style="background:#1a7bb5"></span><span style="background:#f26522"></span><span style="background:#d9261c"></span>
  </div>
</section>

<section class="box newsletter">
  <h2><em>GET TIPS AND TRICKS!</em> SUBSCRIBE TO OUR NEWSLETTER</h2>
  <div class="signup"><div class="field">your email id</div><div class="btn">Subscribe</div></div>
</section>

<main class="welcome">
  <h1>WELCOME TO MAPLE BEACON</h1>
  <h3>Our Mission</h3>
  <p>Etiam adipiscing mollis nulla, ac bibendum elit commodo ac. Pellentesque vehicula sodales vulputate. Suspendisse vel semper tortor. Duis tristique pharetra ligula sed bibendum. Etiam adipiscing mollis nulla, ac bibendum elit commodo ac. Etiam adipiscing mollis nulla, ac bibendum elit commodo ac.</p>
  <ul class="ticks">
    <li><svg viewBox="0 0 20 20"><rect width="20" height="20" rx="3" fill="#8dc63f"/><path d="M5 10l3.5 3.5L15 7" fill="none" stroke="#fff" stroke-width="2.6"/></svg>Nam ac risus metus, sit amet blandit ante.</li>
    <li><svg viewBox="0 0 20 20"><rect width="20" height="20" rx="3" fill="#8dc63f"/><path d="M5 10l3.5 3.5L15 7" fill="none" stroke="#fff" stroke-width="2.6"/></svg>Nunc adipiscing, ipsum eu scelerisque euismod, diam nisl condimentum neque,</li>
    <li><svg viewBox="0 0 20 20"><rect width="20" height="20" rx="3" fill="#8dc63f"/><path d="M5 10l3.5 3.5L15 7" fill="none" stroke="#fff" stroke-width="2.6"/></svg>Vel gravida ligula velit vitae nisl. Pellentesque at dignissim ipsum. Vivamus id massa arcu.</li>
    <li><svg viewBox="0 0 20 20"><rect width="20" height="20" rx="3" fill="#8dc63f"/><path d="M5 10l3.5 3.5L15 7" fill="none" stroke="#fff" stroke-width="2.6"/></svg>Phasellus feugiat condimentum neque ac bibendum.</li>
    <li><svg viewBox="0 0 20 20"><rect width="20" height="20" rx="3" fill="#8dc63f"/><path d="M5 10l3.5 3.5L15 7" fill="none" stroke="#fff" stroke-width="2.6"/></svg>Pellentesque dictum lectus sapien, eu pulvinar eros.</li>
  </ul>
  <p class="closing">Maecenas lacinia, nulla at interdum dapibus, velit sapien posuere eros, et hendrerit purus erat quis est. Proin commodo blandit mauris sed convallis. Donec tellus metus, feugiat sed condimentum congue, dignissim ut leo.</p>
</main>

<div class="quote">Get a Free Quote!</div>

<footer class="footer">
  <nav class="footnav"><span>Site Map</span><span>Strategy</span><span>Portfolio</span><span>About Us</span><span>Contact Us</span><span>Blog</span></nav>
  <div class="copy">©MAPLE BEACON INC. 2013</div>
  <div class="footer-contact">
    <svg viewBox="0 0 16 12"><path d="M0 0h16v12H0z M0 0l8 6 8-6" stroke="#777" stroke-width="1"/></svg>info@maplebeacon.example |
    <svg viewBox="0 0 16 16"><path d="M3 1l3 3-2 2c1 2 3 4 5 5l2-2 3 3-2 3C7 14 2 9 0 3z"/></svg><span class="phone">587-555-0142</span>
  </div>
</footer>
</body>
</html>
```